Window Treatment business needs website redesigned.

We need a revamp and refresh of our current site www.velmarix.ca
Looking to attract very high end customer. It should be a very simple design with very little text. This site will be visited by prospective homeowners, designers, builders and architects. They should feel that they are dealing with a high-end product selection, where experience, customer service and unique product offering is the focus. The content will be to highlight our services and highlight the manufacturers we sell, using a few rich photos to highlight the products. We should NOT look like we are a very large company. It should NOT have discounts/savings buttons and many menus to choose from. We offer over 15 years experience to narrow the many market options, to provide the right technical solution.
We specialize in products that are not readily available on the market and specifically motorized systems for indoors and outdoors.
Our main suppliers are Kravenholt.com, Dimbrell.com
We carry our own locally manufactured product line of roller shades.
Main product pictures should be of roller shades, outdoor bug screens, awnings and outdoor pergolas.

Reason: I understand that Christmas is coming up real short and many people are extremely busy. If you have a CREATIVE gifting you still want to submit, I look forward to your idea!

Reason: Due to holiday season, we have not had sufficient time to review to make a final decision. Thank you for your patience!

Target Market(s)

High end home owners, designers, builders, architects

Industry/Entity Type

Contractor

Coding

Coded - Design and coding required

Number of Pages Required

3 page

Font styles to use
Sans Serif

Requirements
Must have
• Landing page with full size image like homepage of zolvane.it
• Products page that highlights products with simple product shot image, description and link to manufacturer.
• On main page a scrolling of customer reviews.
• I want a very simple, eye-catching, emotional image for homepage. It does not need to include any product image.
• An image that shows technology combining/meshing with hand craftsmanship.
• Focus is on design.
• http://www.zolvane.it/en/gallery is a great layout and design.
Nice to have
• Logo shape for icons and watermark should be used.
• Look like and have simple motion effects like quorix.com or telvarin.com
Should not have
• Generic/standard looking feel like bluppet.com or mecklorwindow.ca
• No use of green as background only subtle text.
• Lots of text and pages.

```html
<!DOCTYPE html>
<html lang="en">
<head>
<meta charset="utf-8">
<title>Velmarix — Window Treatment Solutions</title>
<link href="https://fonts.googleapis.com/css2?family=Oswald:wght@300;400;500&family=Open+Sans:wght@400;600;700&display=swap" rel="stylesheet">
<style>
:root{
  --green:#62c13b;
  --green-dark:#3f9a22;
  --ink:#1f1f1f;
  --charcoal:#262626;
  --charcoal-2:#2f2f2f;
  --stone:#3a3a3a;
  --paper:#e4e4e2;
  --white:#ffffff;
  --soft:#d8d8d8;
  --muted:#bdbdbd;
}
*{box-sizing:border-box;margin:0;padding:0}
html,body{width:1200px;height:4348px;overflow:hidden;background:var(--charcoal)}
body{font-family:"Open Sans",Arial,sans-serif;color:var(--white);position:relative}
.section{position:absolute;left:0;width:1200px;overflow:hidden}
.abs{position:absolute}
.heading{font-family:"Oswald",Arial,sans-serif;font-weight:400;text-transform:uppercase;line-height:1}
.heading .accent{color:var(--green)}
.btn-pill{display:inline-block;border:2px solid #9a9a9a;border-radius:30px;color:var(--white);font-size:17px;padding:12px 30px;text-transform:uppercase;line-height:1}

/* header */
.site-header{top:0;height:128px;background:var(--white)}
.brand{left:78px;top:26px;display:flex;align-items:center;gap:16px}
.brand-mark{width:76px;height:76px;border-radius:50%;background:var(--ink)}
.brand-name{font-family:"Oswald",Arial,sans-serif;font-size:48px;font-weight:400;color:var(--ink);line-height:1}
.brand-tag{font-size:14px;color:var(--green-dark);margin-top:4px}
.main-nav{right:78px;top:50px;display:flex;gap:38px;font-size:19px;text-transform:uppercase}
.main-nav a{color:#555;text-decoration:none}
.main-nav a.is-active{color:var(--green)}

/* hero */
.hero{top:128px;height:684px}
.hero-photo{inset:0;background:linear-gradient(160deg,#e9e6df 0%,#c9b8a0 30%,#8a6a4c 55%,#d8d2c7 75%,#7d7a6a 100%)}
.hero-title{left:0;width:1200px;top:137px;text-align:center;font-family:"Oswald",Arial,sans-serif;font-size:72px;color:var(--green);font-weight:500;line-height:1}
.hero-sub{left:0;width:1200px;top:222px;text-align:center;font-size:31px;font-weight:700;line-height:1.2;text-shadow:0 2px 6px rgba(0,0,0,.6)}
.hero-cta{left:520px;top:305px;width:178px;height:56px;border-radius:30px;background:var(--ink);color:var(--white);font-size:19px;text-align:center;line-height:56px;text-transform:uppercase}

/* welcome */
.welcome{top:812px;height:463px;background:var(--charcoal)}
.welcome h2{left:78px;top:60px;font-size:70px}
.welcome p{left:78px;top:156px;width:610px;font-size:15.5px;line-height:1.75;color:#e6e6e6}
.welcome .btn-pill{position:absolute;left:78px;top:340px}
.welcome-badge{left:750px;top:45px;width:290px;height:290px;border-radius:50%;background:var(--white);display:flex;align-items:center;justify-content:center}
.welcome-badge span{font-family:"Oswald",Arial,sans-serif;font-size:50px;color:var(--ink)}

/* services */
.services{top:1275px;height:638px}
.services-photo{inset:0;background:linear-gradient(180deg,#4a4a48 0%,#363634 50%,#2a2a29 100%)}
.services h2{left:0;width:1200px;top:112px;text-align:center;font-size:70px}
.services .lead{left:170px;width:860px;top:200px;text-align:center;font-size:19px;line-height:1.5;color:#e6e6e6}
.service{top:284px;width:240px;text-align:center}
.service-icon{width:128px;height:128px;border-radius:50%;background:var(--white);margin:0 auto;display:flex;align-items:center;justify-content:center}
.service h3{font-weight:400;font-size:22px;margin-top:20px;color:var(--green)}
.service p{font-size:17px;font-weight:700;line-height:1.4;margin-top:10px;color:#e6e6e6}

/* products */
.products{top:1913px;height:697px;background:var(--paper)}
.products h2{left:0;width:1200px;top:80px;text-align:center;font-size:76px;color:var(--ink)}
.products .lead{left:300px;width:600px;top:170px;text-align:center;font-size:21px;color:var(--ink);line-height:1.45}
.product{top:275px;width:241px;height:228px}
.product-photo{width:241px;height:188px}
.product-label{height:40px;background:var(--ink);color:var(--white);text-align:center;line-height:40px;font-size:17px}
.products-more{left:493px;top:565px;width:214px;height:59px;border:4px solid var(--ink);color:var(--ink);font-size:18px;display:flex;align-items:center;justify-content:center;gap:14px;text-transform:uppercase}

/* testimonial */
.testimonial{top:2610px;height:490px}
.testimonial-photo{inset:0;background:linear-gradient(180deg,#2b2a26 0%,#3a3731 50%,#26241f 100%)}
.testimonial h2{left:0;width:1200px;top:62px;text-align:center;font-size:38px;color:var(--green);font-weight:400;line-height:1}
.avatar{left:530px;top:122px;width:140px;height:140px;border-radius:50%;border:5px solid var(--white);background:linear-gradient(180deg,#9b8f86,#4b4440)}
.testimonial .quote{left:270px;width:660px;top:282px;text-align:center;font-size:16px;line-height:1.6}
.testimonial .cite{left:0;width:1200px;top:352px;text-align:center;font-size:14px;color:var(--green);text-transform:uppercase}

/* gallery */
.gallery{top:3100px;height:550px;background:var(--charcoal)}
.gallery h2{left:78px;top:66px;font-size:38px;font-weight:400;line-height:1}
.gallery-brand{left:78px;top:125px;width:360px;text-align:center}
.gallery-brand .mark{width:150px;height:150px;border-radius:50%;background:var(--white);margin:0 auto}
.gallery-brand .name{font-family:"Oswald",Arial,sans-serif;font-size:68px;margin-top:14px;line-height:1}
.gallery-brand .tag{font-size:22px;font-weight:600;margin-top:6px}
.gallery-brand p{font-size:15px;line-height:1.5;margin-top:12px;text-align:left;padding-left:20px}
.thumb{width:166px;height:166px;border-radius:50%}

/* newsletter */
.newsletter{top:3650px;height:207px;background:var(--charcoal-2)}
.newsletter h2{left:78px;top:36px;font-family:"Open Sans",Arial,sans-serif;font-size:25px;font-weight:600;text-transform:uppercase;color:var(--green);line-height:1.2}
.newsletter p{left:78px;top:76px;width:420px;font-size:16px;line-height:1.5;color:#e6e6e6}
.signup{left:538px;top:50px;display:flex}
.signup-field{width:285px;height:62px;background:var(--white);color:#888;font-size:15px;display:flex;align-items:center;gap:10px;padding-left:18px}
.signup-btn{width:136px;height:62px;background:var(--ink);font-size:18px;line-height:62px;text-align:center;text-transform:uppercase}

/* footer */
.footer{top:3857px;height:433px;background:#1c1c1c}
.footer-photo{inset:0;background:linear-gradient(180deg,#3a3530 0%,#1f1d1b 60%,#1a1a1a 100%)}
.footer h4{font-weight:400;font-size:22px;text-transform:uppercase;line-height:1.2}
.footer ul{list-style:none;font-size:16px;line-height:1.6}
.contact-row{display:flex;gap:26px;font-size:15px;line-height:1.55;align-items:flex-start}
.quote-field{width:260px;height:38px;background:var(--white);color:#777;font-size:14px;padding:0 10px;line-height:38px;margin-bottom:9px}
.quote-btn{width:142px;height:44px;border:2px solid var(--green);color:var(--green);font-size:18px;text-align:center;line-height:40px;text-transform:uppercase}
.partner{background:#d9d9d9;border-radius:4px}
.social{width:36px;height:36px;border-radius:50%;background:#555}
.copyright{top:4290px;height:58px;background:var(--ink);color:#cfcfcf;border-top:1px solid #333}
.copyright p{left:78px;top:18px;font-size:16px}
.copyright strong{color:var(--green)}
.socials{right:70px;top:11px;display:flex;gap:12px}
</style>
</head>
<body>

<header class="section site-header">
  <div class="abs brand">
    <div class="brand-mark"></div>
    <div>
      <div class="brand-name">Velmarix</div>
      <div class="brand-tag">Window Treatment Solutions</div>
    </div>
  </div>
  <nav class="abs main-nav">
    <a class="is-active" href="#">Home</a><a href="#">About</a><a href="#">Services</a><a href="#">Products</a><a href="#">Gallery</a><a href="#">Contact</a>
  </nav>
</header>

<section class="section hero">
  <div class="abs hero-photo" role="img" aria-label="Sunlit covered patio with white shutters, hanging plants and a dining set under a pergola"></div>
  <svg class="abs" style="left:0;top:0" width="1200" height="684" viewBox="0 0 1200 684">
    <polygon points="0,560 330,640 760,500 1200,600 1200,684 0,684" fill="#ffffff" opacity=".35"/>
    <polygon points="0,590 330,660 760,520 1200,620 1200,684 0,684" fill="#262626"/>
    <polyline points="0,590 330,660 760,520 1200,620" fill="none" stroke="#62c13b" stroke-width="3"/>
  </svg>
  <div class="abs hero-title">VELMARIX</div>
  <div class="abs hero-sub">Specializing in Motorized systems for<br>indoors and outdoors</div>
  <div class="abs hero-cta">Contact Us</div>
</section>

<section class="section welcome">
  <h2 class="abs heading"><span class="accent">Welcome</span> Velmarix</h2>
  <p class="abs">Lorem Ipsum is simply dummy text of the printing and typesetting industry. Lorem Ipsum has been the industry's standard dummy text ever since the 1500s, when an unknown printer took a galley of type and scrambled it to make a type specimen book. It has survived not only five centuries, but also the leap into electronic typesetting, remaining essentially unchanged.</p>
  <span class="btn-pill">Read More</span>
  <div class="abs welcome-badge"><span>Velmarix</span></div>
</section>

<section class="section services">
  <div class="abs services-photo" role="img" aria-label="Modern house facade with exterior shades, darkened"></div>
  <svg class="abs" style="left:0;top:0" width="1200" height="638" viewBox="0 0 1200 638">
    <polygon points="0,0 1200,0 1200,30 700,0 380,80 0,30" fill="#262626"/>
    <polyline points="0,30 380,80 700,0 1200,30" fill="none" stroke="#62c13b" stroke-width="3"/>
    <polygon points="0,638 0,600 500,560 880,620 1200,540 1200,638" fill="#e4e4e2"/>
  </svg>
  <h2 class="abs heading">Our Services</h2>
  <p class="abs lead">Lorem Ipsum is simply dummy text of the printing and typesetting industry. Lorem Ipsum has been the industry's standard dummy text ever since the 1500.</p>

  <div class="abs service" style="left:86px">
    <div class="service-icon"><svg width="60" height="60" viewBox="0 0 60 60" fill="none" stroke="#1f1f1f" stroke-width="3"><rect x="8" y="6" width="44" height="6" fill="#1f1f1f"/><rect x="12" y="12" width="36" height="32"/><line x1="12" y1="22" x2="48" y2="22"/><line x1="12" y1="32" x2="48" y2="32"/><line x1="30" y1="44" x2="30" y2="54"/></svg></div>
    <h3>Roller Shades</h3>
    <p>Lorem Ipsum is simply dummy text of the printing</p>
  </div>
  <div class="abs service" style="left:349px">
    <div class="service-icon"><svg width="60" height="60" viewBox="0 0 60 60" fill="none" stroke="#1f1f1f" stroke-width="3"><line x1="6" y1="8" x2="54" y2="8"/><path d="M10 8 C10 30 20 40 22 54 L10 54 Z" fill="#1f1f1f"/><path d="M50 8 C50 30 40 40 38 54 L50 54 Z" fill="#1f1f1f"/></svg></div>
    <h3>Drapery</h3>
    <p>Lorem Ipsum is simply dummy text of the printing</p>
  </div>
  <div class="abs service" style="left:607px">
    <div class="service-icon"><svg width="60" height="60" viewBox="0 0 60 60" fill="none" stroke="#1f1f1f" stroke-width="3"><circle cx="30" cy="30" r="22"/><path d="M18 30 h24 M24 22 v16 M36 22 v16"/></svg></div>
    <h3>Outdoor bug screens</h3>
    <p>Lorem Ipsum is simply dummy text of the printing</p>
  </div>
  <div class="abs service" style="left:874px">
    <div class="service-icon"><svg width="60" height="60" viewBox="0 0 60 60" fill="#1f1f1f"><path d="M8 10 h44 l4 12 H4 Z"/><rect x="10" y="26" width="40" height="26"/><rect x="18" y="32" width="10" height="20" fill="#fff"/><rect x="33" y="32" width="10" height="10" fill="#fff"/></svg></div>
    <h3>Awnings</h3>
    <p>Lorem Ipsum is simply dummy text of the printing</p>
  </div>
</section>

<section class="section products">
  <h2 class="abs heading" style="color:var(--ink)">Our <span class="accent">Products</span></h2>
  <p class="abs lead">Lorem Ipsum is simply dummy text of the printing and typesetting industry.</p>
  <div class="abs product" style="left:78px"><div class="product-photo" role="img" aria-label="Living room with roller shades" style="background:linear-gradient(160deg,#b9a68c,#5c4f42)"></div><div class="product-label">Roller shades</div></div>
  <div class="abs product" style="left:347px"><div class="product-photo" role="img" aria-label="Terrace with outdoor bug screens over a lake view" style="background:linear-gradient(170deg,#d9c2a0,#8aa7b8 55%,#4d5d3c)"></div><div class="product-label">Outdoor bug screens</div></div>
  <div class="abs product" style="left:615px"><div class="product-photo" role="img" aria-label="House with striped retractable awnings" style="background:linear-gradient(170deg,#c9d6e4,#b26b48 50%,#5f7c3e)"></div><div class="product-label">Awnings</div></div>
  <div class="abs product" style="left:883px"><div class="product-photo" role="img" aria-label="Garden pergola with seating" style="background:linear-gradient(170deg,#a9c07a,#5f7d3c 55%,#3a3a30)"></div><div class="product-label">Outdoor pergolas</div></div>
  <div class="abs products-more">Read More <svg width="48" height="14" viewBox="0 0 48 14"><line x1="0" y1="7" x2="44" y2="7" stroke="#1f1f1f" stroke-width="2.5"/><polyline points="38,1 45,7 38,13" fill="none" stroke="#1f1f1f" stroke-width="2.5"/></svg></div>
</section>

<section class="section testimonial">
  <div class="abs testimonial-photo" role="img" aria-label="Dim living room with tall windows and shades"></div>
  <h2 class="abs">TESTIMONIAL</h2>
  <div class="abs avatar" role="img" aria-label="Client portrait"></div>
  <p class="abs quote">Lorem Ipsum is simply dummy text of the printing and typesetting industry. Lorem Ipsum has been the industry's standard dummy text ever since the 1500s.</p>
  <p class="abs cite">- Client Name</p>
  <svg class="abs" style="left:0;top:0" width="1200" height="490" viewBox="0 0 1200 490">
    <polygon points="0,420 440,480 800,390 1200,450 1200,490 0,490" fill="#262626"/>
    <polyline points="0,420 440,480 800,390 1200,450" fill="none" stroke="#62c13b" stroke-width="3"/>
  </svg>
</section>

<section class="section gallery">
  <h2 class="abs">OUR GALLERY</h2>
  <div class="abs gallery-brand">
    <div class="mark"></div>
    <div class="name">Velmarix</div>
    <div class="tag">Window Treatment Solutions</div>
    <p>Lorem Ipsum is simply dummy text of the printing and typesetting industry.</p>
  </div>
  <div class="abs thumb" style="left:520px;top:108px;background:linear-gradient(160deg,#e07a2a,#f4f1ec)" role="img" aria-label="Orange roller shades in a bright room"></div>
  <div class="abs thumb" style="left:737px;top:108px;background:linear-gradient(160deg,#9fb4c8,#7a6a55)" role="img" aria-label="House exterior with awnings"></div>
  <div class="abs thumb" style="left:955px;top:108px;background:linear-gradient(160deg,#3c3a36,#8a6a4a)" role="img" aria-label="Outdoor lounge under a pergola at dusk"></div>
  <div class="abs thumb" style="left:520px;top:298px;background:linear-gradient(160deg,#e6e4de,#8d8e86)" role="img" aria-label="Sheer shades on large windows"></div>
  <div class="abs thumb" style="left:737px;top:298px;background:linear-gradient(160deg,#f0c46a,#5a4a3a)" role="img" aria-label="Warmly lit interior with shades"></div>
  <div class="abs thumb" style="left:955px;top:298px;background:linear-gradient(160deg,#d8e7f2,#6f9ec6)" role="img" aria-label="Glass roof with retractable shade"></div>
</section>

<section class="section newsletter">
  <h2 class="abs">Stay Tuned With Us</h2>
  <p class="abs">Subscribe now and receive weekly newsletter with educational materials,new courses, interesting posts, popular books and much more!</p>
  <div class="abs signup">
    <div class="signup-field"><svg width="20" height="14" viewBox="0 0 20 14" fill="none" stroke="#888" stroke-width="1.5"><rect x="1" y="1" width="18" height="12"/><polyline points="1,1 10,8 19,1"/></svg>Enter Email id :</div>
    <div class="signup-btn">Subscribe</div>
  </div>
  <svg class="abs" style="left:0;top:0" width="1200" height="207" viewBox="0 0 1200 207">
    <polygon points="0,207 0,185 380,160 720,207" fill="#1c1c1c"/>
    <polygon points="720,207 980,160 1200,190 1200,207" fill="#1c1c1c"/>
    <polyline points="0,185 380,160 720,207 980,160 1200,190" fill="none" stroke="#62c13b" stroke-width="2"/>
  </svg>
</section>

<footer class="section footer">
  <div class="abs footer-photo" role="img" aria-label="Dark room with window shades"></div>
  <div class="abs" style="left:78px;top:20px">
    <h4>Useful Links</h4>
    <ul style="margin-top:12px"><li>Home</li><li>About</li><li>Services</li><li>Products</li><li>Gallery</li><li>Contact</li></ul>
  </div>
  <div class="abs" style="left:275px;top:20px">
    <h4>Contact Info</h4>
    <div class="contact-row" style="margin-top:18px">
      <svg width="18" height="24" viewBox="0 0 18 24" fill="#fff"><path d="M9 0a9 9 0 0 0-9 9c0 7 9 15 9 15s9-8 9-15a9 9 0 0 0-9-9zm0 12a3 3 0 1 1 0-6 3 3 0 0 1 0 6z"/></svg>
      <div>27B-14 Harlow Crescent,<br>Toronto, ON, M4K 2T8<br><u>VIEW MAP</u></div>
    </div>
    <div class="contact-row" style="margin-top:24px">
      <svg width="20" height="20" viewBox="0 0 20 20" fill="#fff"><path d="M4 1l4 4-2 3c1 2 3 4 6 6l3-2 4 4-3 3C9 19 1 11 1 4z"/></svg>
      <div>416-555-0142</div>
    </div>
    <div class="contact-row" style="margin-top:24px">
      <svg width="20" height="14" viewBox="0 0 20 14" fill="none" stroke="#fff" stroke-width="1.5"><rect x="1" y="1" width="18" height="12"/><polyline points="1,1 10,8 19,1"/></svg>
      <div>hello@velmarix.ca</div>
    </div>
  </div>
  <div class="abs" style="left:550px;top:20px">
    <h4>Get a Free Quote</h4>
    <div style="margin-top:16px">
      <div class="quote-field">Enter Name</div>
      <div class="quote-field">Enter Email</div>
      <div class="quote-field">Enter Contact No.</div>
      <div class="quote-field" style="height:54px">Enter Message</div>
      <div class="quote-btn">Submit</div>
    </div>
  </div>
  <div class="abs partner" style="left:885px;top:38px;width:195px;height:62px"></div>
  <div class="abs partner" style="left:948px;top:112px;width:175px;height:36px"></div>
  <div class="abs partner" style="left:845px;top:110px;width:88px;height:120px;border-radius:44px"></div>
  <div class="abs partner" style="left:948px;top:160px;width:165px;height:60px"></div>
  <div class="abs partner" style="left:948px;top:232px;width:170px;height:50px"></div>
  <div class="abs partner" style="left:855px;top:250px;width:80px;height:30px"></div>
</footer>

<div class="section copyright">
  <p class="abs"><strong>© VELMARIX</strong> 2016, All Rights Reserved</p>
  <div class="abs socials">
    <div class="social"></div><div class="social"></div><div class="social"></div><div class="social"></div><div class="social"></div>
  </div>
</div>

</body>
</html>
```